Construction Company Cellar Crafters needs Business Card

I would like modern looking business card design. I am attaching logo of our company. Please include cell nr 302.418.7650 , email address cellarcrafters4u@examplemail.com, web : cellarcrafters4u.com, please also include wording: Specializing in finishing and remodeling basements. You can play with dark grey and orange colors or any ideas are welcome. Also include social media icons Friendloop and HouseGuidr.

```html
<!DOCTYPE html>
<html lang="en">
<head>
<meta charset="utf-8">
<title>Cellar Crafters – Business Card</title>
<link href="https://fonts.googleapis.com/css2?family=Source+Sans+3:ital,wght@0,400;0,600;1,400&display=swap" rel="stylesheet">
<style>
  :root {
    --bg-top: #a9a9a9;
    --bg-bottom: #8d8d8d;
    --card-light: #ffffff;
    --card-dark: #151515;
    --orange: #f05a28;
    --ink: #2b2b2b;
    --rule: #f4b9a2;
  }
  * { margin: 0; padding: 0; box-sizing: border-box; }
  html, body { width: 1200px; height: 900px; overflow: hidden; }
  body {
    background: linear-gradient(180deg, var(--bg-top), var(--bg-bottom));
    font-family: "Source Sans 3", "Helvetica Neue", Arial, sans-serif;
    position: relative;
  }
  .card {
    position: absolute;
    top: 306px;
    width: 440px;
    height: 271px;
    border-radius: 10px;
  }
  .card--front { left: 149px; background: var(--card-light); }
  .card--back { left: 608px; background: var(--card-dark); }

  .brand-name {
    position: absolute;
    color: var(--orange);
    font-weight: 600;
    letter-spacing: 1px;
    text-transform: uppercase;
    white-space: nowrap;
  }
  .card--front .brand-name { left: 27px; top: 80px; font-size: 38px; line-height: 1; }
  .card--back .brand-name { left: 0; right: 0; top: 122px; text-align: center; font-size: 38px; line-height: 1; }

  .person { position: absolute; right: 24px; top: 151px; text-align: right; }
  .person__name { color: var(--orange); font-weight: 600; font-size: 15px; line-height: 18px; }
  .person__title { color: var(--ink); font-size: 12.5px; line-height: 15px; }

  .divider {
    position: absolute; left: 28px; right: 24px; top: 193px;
    height: 1px; background: var(--rule);
  }

  .contacts { position: absolute; left: 26px; top: 199px; list-style: none; }
  .contacts li {
    display: flex; align-items: center; gap: 7px;
    color: var(--ink); font-size: 12.5px; line-height: 16px;
  }
  .contacts svg { width: 9px; height: 9px; fill: var(--orange); flex: none; }

  .socials {
    position: absolute; right: 24px; top: 214px;
    display: flex; flex-direction: column; align-items: flex-end; gap: 3px;
  }
  .social {
    display: flex; align-items: center; gap: 4px;
    color: var(--orange); font-weight: 600; font-size: 11px; line-height: 13px;
  }
  .social::before {
    content: ""; width: 8px; height: 8px; background: var(--orange);
  }

  .tagline {
    position: absolute; left: 0; right: 0; top: 226px;
    text-align: center; color: var(--orange);
    font-style: italic; font-size: 11.5px; letter-spacing: 0.1px;
    text-transform: uppercase;
  }
</style>
</head>
<body>
  <section class="card card--front" aria-label="Card front">
    <div class="brand-name">Cellar Crafters</div>
    <div class="person">
      <div class="person__name">Daniel Harper</div>
      <div class="person__title">Managing Director</div>
    </div>
    <div class="divider"></div>
    <ul class="contacts">
      <li>
        <svg viewBox="0 0 10 10" aria-hidden="true"><path d="M2 0.5l1.6 2.3-1 1c.6 1.3 1.5 2.2 2.7 2.8l1-1 2.2 1.5-.8 1.6C4.6 8.6 1.3 5.5.5 2z"/></svg>
        302.418.7650
      </li>
      <li>
        <svg viewBox="0 0 10 10" aria-hidden="true"><path d="M0 2h10v1L5 6 0 3z M0 4l5 3 5-3v4H0z"/></svg>
        cellarcrafters4u@examplemail.com
      </li>
      <li>
        <svg viewBox="0 0 10 10" aria-hidden="true"><circle cx="5" cy="5" r="4.5"/></svg>
        cellarcrafters4u.com
      </li>
    </ul>
    <div class="socials">
      <span class="social">Friendloop</span>
      <span class="social">HouseGuidr</span>
    </div>
  </section>

  <section class="card card--back" aria-label="Card back">
    <div class="brand-name">Cellar Crafters</div>
    <p class="tagline">Specializing in finishing and remodeling basements.</p>
  </section>
</body>
</html>
```